Website for International Non-Profit for Birth Parent Searching

LumaKin is a 501(c)(3) non-profit organization that helps Chinese adoptees search and reunite with birth families who were separated due the One Child Policy in China. We want to create a website that can link to an information database that allows website users to easily access information around search ads in an organized way; help connect families to professional searchers; provide resources for community support for adoptees and their families as they embark on a personal and emotional journey of finding birth family through support groups on social media and consultation/education on the searching process; and provide the opportunity for the adoptive community to give back through donations and volunteer opportunities. The final design should foster a sense of community and be easy navigable to access the multiple resources we provide to help families search for each other. We would like to see designs with red/black/white color schemes that are gentle, inviting, and family friendly to viewers. We would like to see some design layouts with Chinese themes, if possible.

```html
<!DOCTYPE html>
<html lang="en">
<head>
<meta charset="utf-8">
<title>LumaKin – International Non-Profit for Birth Parent Searching</title>
<link href="https://fonts.googleapis.com/css2?family=Rubik:wght@400;500;600&family=Open+Sans:wght@400;600&display=swap" rel="stylesheet">
<style>
:root{
  --red:#d90000;
  --ink:#111111;
  --text:#333333;
  --soft:#f4f0f0;
  --white:#ffffff;
  --rule:#bdbdbd;
  --footer:#2b2b2b;
  --footer-text:#d8d8d8;
}
*{box-sizing:border-box;margin:0;padding:0}
html,body{width:1200px;height:3538px;overflow:hidden}
body{font-family:"Open Sans",sans-serif;color:var(--text);background:var(--white);position:relative}
.abs{position:absolute}
h1,h2,h3,h4,.head{font-family:"Rubik",sans-serif;color:var(--ink)}
.btn{display:inline-block;background:var(--red);color:var(--white);font-family:"Rubik",sans-serif;font-weight:500;font-size:14px;padding:9px 16px;letter-spacing:.2px}
.rule{width:112px;height:2px;background:var(--rule)}
.rule.center{margin:0 auto}

/* header */
.site-header{top:0;left:0;width:1200px;height:74px}
.brand{left:132px;top:16px;font-family:"Rubik",sans-serif;font-weight:500;font-size:31px;color:var(--ink)}
.nav{left:330px;top:28px;display:flex;gap:32px;font-family:"Rubik",sans-serif;font-size:13px;color:var(--ink)}
.nav .active{color:var(--red);text-decoration:underline;font-weight:500}
.call{left:915px;top:20px;display:flex;gap:12px;align-items:center}
.call small{display:block;font-family:"Rubik",sans-serif;font-size:10px;font-weight:500;color:var(--ink)}
.call strong{font-family:"Rubik",sans-serif;font-size:17px;font-weight:600;color:var(--ink)}

/* hero */
.hero{top:74px;left:0;width:1200px;height:550px;background:linear-gradient(100deg,#6f8a4e 0%,#c9c0ae 30%,#a89a86 55%,#5c6548 80%,#3a3f2a 100%)}
.hero-panel{left:596px;top:130px;width:439px;height:224px;background:rgba(40,40,40,.86);padding:26px 34px}
.hero-panel h1{color:var(--white);font-size:32px;font-weight:600;line-height:40px}
.hero-panel .btn{margin-top:14px;font-size:15px;padding:9px 18px}
.dots{left:574px;top:500px;display:flex;gap:9px;align-items:center}
.dots i{width:7px;height:7px;border-radius:50%;background:var(--white)}
.dots i.on{width:12px;height:12px;background:none;border:2px solid var(--white)}

/* welcome */
.welcome h2{left:136px;top:674px;font-size:24px;font-weight:500}
.welcome .rule{left:138px;top:710px}
.welcome p{left:139px;top:748px;width:365px;font-size:14px;line-height:21.5px}
.welcome .btn{left:141px;top:958px}
.welcome .photo{left:562px;top:676px;width:506px;height:332px;background:linear-gradient(180deg,#4f8fd6 0%,#a9c9ea 45%,#8a7f6a 75%,#b6382f 100%)}

/* organized */
.band-soft{left:0;width:1200px;background:var(--soft)}
.section-title{width:1200px;left:0;text-align:center;font-size:24px;font-weight:500}
.card{background:var(--white)}
.org-card{top:1180px;width:297px;height:345px;text-align:center;padding-top:38px}
.org-card .icon{width:90px;height:90px;border-radius:50%;background:#222;margin:0 auto 28px;display:flex;align-items:center;justify-content:center}
.org-card p{font-size:14px;line-height:19.5px;width:232px;margin:0 auto}

/* split */
.split-photo{left:0;top:1577px;width:634px;height:425px;background:linear-gradient(110deg,#7a8a45 0%,#c7b98a 40%,#e9ddc6 60%,#8fa05a 100%)}
.split h3{left:691px;top:1636px;width:340px;font-size:20px;font-weight:500;line-height:25.5px}
.split p{left:694px;top:1730px;width:365px;font-size:14px;line-height:21.5px}
.split .btn{left:697px;top:1912px}

/* testimonials */
.quote{top:2138px;width:298px;height:294px;border:1px solid #dcdcdc;text-align:center;padding-top:28px}
.quote .mark{font-family:Georgia,serif;font-size:34px;color:#bbb;line-height:30px}
.quote p{font-size:14px;line-height:17.5px;width:220px;margin:10px auto 0}
.quote .bar{width:30px;height:2px;background:var(--red);margin:26px auto 22px}
.quote h4{font-size:14px;font-weight:500}
.quote small{display:block;font-size:12px;margin-top:5px;color:var(--ink)}

/* blog */
.post{top:2610px;width:298px;height:332px;border:1px solid #d0d0d0}
.post .thumb{height:172px}
.post .body{padding:26px 24px 0}
.post h4{font-size:12.5px;font-weight:500;letter-spacing:.1px}
.post p{font-size:11.5px;line-height:14.5px;margin-top:8px;color:#222}
.post .btn{font-size:11px;padding:6px 10px;margin-top:14px}

/* cta */
.cta{top:2990px;left:0;width:1200px;height:217px;background:linear-gradient(90deg,#3d3d36 0%,#2a2a25 50%,#161614 100%);text-align:center}
.cta h2{color:#e6e6e6;font-weight:400;font-size:20px;line-height:29px;padding-top:52px;letter-spacing:.3px}
.cta .btn-light{display:inline-block;background:var(--white);color:var(--ink);font-family:"Rubik",sans-serif;font-weight:500;font-size:15px;padding:9px 17px;margin-top:14px}

/* footer */
.site-footer{top:3207px;left:0;width:1200px;height:331px;background:var(--footer);color:var(--footer-text)}
.foot-brand{left:163px;top:93px;font-family:"Rubik",sans-serif;font-weight:500;font-size:42px;color:var(--white)}
.foot-col h5{font-family:"Rubik",sans-serif;font-size:13px;font-weight:500;color:var(--white);margin-bottom:22px}
.foot-col ul{list-style:none;font-size:11.5px;line-height:19.7px}
.item{display:flex;gap:12px;align-items:flex-start;font-size:11.5px;line-height:15.5px;margin-bottom:21px}
.item .dot{width:24px;height:24px;border-radius:50%;background:var(--white);flex:none;display:flex;align-items:center;justify-content:center}
.foot-line{left:133px;top:258px;width:934px;height:1px;background:#444}
.copy{left:0;top:302px;width:1200px;text-align:center;font-size:9.5px;color:#bbb;padding-right:2px}
</style>
</head>
<body>

<header class="site-header abs">
  <div class="brand abs">LumaKin</div>
  <nav class="nav abs">
    <span class="active">HOME</span><span>ABOUT US</span><span>SERVICES</span><span>BLOG</span><span>TESTIMONIALS</span><span>CONTACT US</span>
  </nav>
  <div class="call abs">
    <svg width="28" height="28" viewBox="0 0 28 28"><circle cx="14" cy="14" r="12.5" fill="none" stroke="#111" stroke-width="1.6"/><path d="M10 8.5c.6-.6 1.4-.5 1.8.2l1 1.8c.3.6.2 1.2-.3 1.6l-.7.6c.6 1.4 1.7 2.5 3.1 3.1l.6-.7c.4-.5 1-.6 1.6-.3l1.8 1c.7.4.8 1.2.2 1.8l-.9.9c-.8.8-2.1.9-3.2.3-2.8-1.5-4.8-3.5-6.2-6.2-.6-1.1-.5-2.4.3-3.2z" fill="#111"/></svg>
    <div><small>CALL US</small><strong>555.014.2290</strong></div>
  </div>
</header>

<section class="hero abs" role="img" aria-label="Photo of a smiling family of three walking in front of a suburban house">
  <div class="hero-panel abs">
    <h1>INTERNATIONAL<br>NON-PROFIT FOR BIRTH<br>PARENT SEARCHING</h1>
    <span class="btn">READ MORE</span>
  </div>
  <div class="dots abs"><i></i><i></i><i class="on"></i><i></i><i></i></div>
</section>

<section class="welcome">
  <h2 class="abs">WELCOME TO LUMAKIN</h2>
  <div class="rule abs"></div>
  <p class="abs">Lorem ipsum dolor sit amet, consectetur adipiscing elit, sed do eiusmod tempor incididunt ut labore et dolore magna aliqua. Ut enim ad minim veniam, quis nostrud exercitation ullamco laboris nisi ut aliquip ex ea commodo consequat. Duis aute irure dolor in repreh enderit in voluptate velit esse cillum dolore eu fugiat nulla pariatur. Excepteur sint occaecat cupidatat non proident, sunt in culpa qui .</p>
  <span class="btn abs">READ MORE</span>
  <div class="photo abs" role="img" aria-label="Photo of a happy family with a small child beside a red car under a blue sky"></div>
</section>

<section>
  <div class="band-soft abs" style="top:1060px;height:517px"></div>
  <h2 class="section-title head abs" style="top:1100px">ORGANIZED WAY</h2>
  <div class="rule abs" style="left:544px;top:1142px"></div>

  <div class="card org-card abs" style="left:131px">
    <div class="icon"><svg width="50" height="50" viewBox="0 0 50 50" fill="#fff"><circle cx="14" cy="9" r="4"/><rect x="9" y="14" width="10" height="16" rx="2"/><rect x="10" y="29" width="3" height="14"/><rect x="15" y="29" width="3" height="14"/><circle cx="36" cy="9" r="4"/><rect x="31" y="14" width="10" height="16" rx="2"/><rect x="32" y="29" width="3" height="14"/><rect x="37" y="29" width="3" height="14"/><circle cx="25" cy="20" r="3"/><rect x="22" y="24" width="6" height="10" rx="1.5"/><rect x="22.5" y="33" width="2" height="9"/><rect x="25.5" y="33" width="2" height="9"/></svg></div>
    <p>Help connect families to professional searchers</p>
  </div>
  <div class="card org-card abs" style="left:451px">
    <div class="icon"><svg width="56" height="56" viewBox="0 0 56 56" fill="#fff"><circle cx="28" cy="10" r="4"/><path d="M21 20a7 5 0 0 1 14 0z"/><circle cx="12" cy="32" r="4"/><path d="M5 42a7 5 0 0 1 14 0z"/><circle cx="44" cy="32" r="4"/><path d="M37 42a7 5 0 0 1 14 0z"/><circle cx="28" cy="38" r="4"/><path d="M21 48a7 5 0 0 1 14 0z"/><path d="M14 22l4-6M42 22l-4-6M20 46l-4-1M36 46l4-1" stroke="#fff" stroke-width="2" fill="none"/></svg></div>
    <p>Provide resources for community support for adoptees and their families as they embark on a personal and emotional journey of finding birth family through support groups on social media and consultation / education on the searching process</p>
  </div>
  <div class="card org-card abs" style="left:771px">
    <div class="icon"><svg width="56" height="60" viewBox="0 0 56 60" fill="#fff"><path d="M25 58V20c0-2 3-2 3 0v-14c0-2 3-2 3 0v14-16c0-2 3-2 3 0v18-12c0-2 3-2 3 0v22c0 6-4 10-6 12v14z"/><path d="M10 58V36c0-2 3-2 3 0v-6c0-2 3-2 3 0v-2c0-2 3-2 3 0v2c0-1 3-1 3 0v12c0 4-3 7-4 9v7z"/><path d="M40 58V40c2-3 4-6 4-8v-6c0-2 3-2 3 0v-2c0-2 3-2 3 0v12c0 4-3 7-4 9v13z"/></svg></div>
    <p style="width:180px">Provide the opportunity for the adoptive community to give back through donations and volunteer opportunities.</p>
  </div>
</section>

<section class="split">
  <div class="split-photo abs" role="img" aria-label="Photo of a smiling mother hugging her young daughter outdoors"></div>
  <h3 class="abs">LOREM IPSUM DOLOR SIT AMET, CONSECTETUR ADIPI SCING ELIT, SED DO EIUSMOD</h3>
  <p class="abs">Lorem ipsum dolor sit amet, consectetur adipiscing elit, sed do eiusmod tempor incididunt ut labore et dolore magna aliqua. Ut enim ad minim veniam, quis nostrud exercitation ullamco laboris nisi ut aliquip ex ea commodo consequat. Duis aute irure dolor in repreh enderit in voluptate velit esse cillum dolore eu fugiat nulla pariatur.</p>
  <span class="btn abs">READ MORE</span>
</section>

<section>
  <div class="band-soft abs" style="top:2002px;height:484px"></div>
  <h2 class="section-title head abs" style="top:2054px">TESTIMONIALS</h2>
  <div class="rule abs" style="left:544px;top:2096px;width:64px"></div>

  <div class="card quote abs" style="left:132px">
    <div class="mark">&ldquo;</div>
    <p>Sed ut perspiciatis unde omnis iste natus error sit voluptatem accusa ntium doloremque laud antium, tota m rem aperiam, eaque ipsa quae ab illo inventore veritatis et quasi architecto</p>
    <div class="bar"></div><h4 class="head">MARLON</h4><small>Willow Creek SA</small>
  </div>
  <div class="card quote abs" style="left:453px">
    <div class="mark">&ldquo;</div>
    <p>Sed ut perspiciatis unde omnis iste natus error sit voluptatem accusa ntium doloremque laud antium, tota m rem aperiam, eaque ipsa quae ab illo inventore veritatis et quasi architecto</p>
    <div class="bar"></div><h4 class="head">MARLON</h4><small>Willow Creek SA</small>
  </div>
  <div class="card quote abs" style="left:771px">
    <div class="mark">&ldquo;</div>
    <p>Sed ut perspiciatis unde omnis iste natus error sit voluptatem accusa ntium doloremque laud antium, tota m rem aperiam, eaque ipsa quae ab illo inventore veritatis et quasi architecto</p>
    <div class="bar"></div><h4 class="head">MARLON</h4><small>Willow Creek SA</small>
  </div>
</section>

<section>
  <h2 class="section-title head abs" style="top:2528px">LATEST BLOG</h2>
  <div class="rule abs" style="left:544px;top:2570px;width:64px"></div>

  <article class="post abs" style="left:132px">
    <div class="thumb" role="img" aria-label="Photo of a father lifting his child in a sunny park" style="background:linear-gradient(120deg,#8fa860,#e8e2c8 50%,#6d8a46)"></div>
    <div class="body"><h4 class="head">SED UT PERSPICIATIS UNDE OMNIS</h4><p>But I must explain to you how all this mis-taken idea of denouncing pleasure and praising pain was born and I will give you</p><span class="btn">READ MORE</span></div>
  </article>
  <article class="post abs" style="left:451px">
    <div class="thumb" role="img" aria-label="Photo of a little girl walking hand in hand with her parents" style="background:linear-gradient(90deg,#cfd6dc,#7a9cc0 45%,#a5b87a 70%,#d9dde0)"></div>
    <div class="body"><h4 class="head">SED UT PERSPICIATIS UNDE OMNIS</h4><p>But I must explain to you how all this mis-taken idea of denouncing pleasure and praising pain was born and I will give you</p><span class="btn">READ MORE</span></div>
  </article>
  <article class="post abs" style="left:771px">
    <div class="thumb" role="img" aria-label="Photo of a family lying together on the grass laughing" style="background:linear-gradient(180deg,#c8d8a0,#8cb056 60%,#5f8a36)"></div>
    <div class="body"><h4 class="head">SED UT PERSPICIATIS UNDE OMNIS</h4><p>But I must explain to you how all this mis-taken idea of denouncing pleasure and praising pain was born and I will give you</p><span class="btn">READ MORE</span></div>
  </article>
</section>

<section class="cta abs" role="img" aria-label="Darkened photo of a family in front of a house behind the call to action">
  <h2>LOREM IPSUM DOLOR SIT AMET, CONSECTETUR ADIPISCING ELIT<br>SED DO EIUSMOD TEMPOR INCIDIDUNT UT LABORE</h2>
  <span class="btn-light">CONTACT US</span>
</section>

<footer class="site-footer abs">
  <div class="foot-brand abs">LumaKin</div>
  <div class="foot-col abs" style="left:442px;top:48px">
    <h5>MENU</h5>
    <ul><li>HOME</li><li>ABOUT US</li><li>SERVICES</li><li>BLOG</li><li>TESTIMONIALS</li><li>CONTACT US</li></ul>
  </div>
  <div class="foot-col abs" style="left:672px;top:48px">
    <h5>CONTACT US</h5>
    <div class="item"><span class="dot"><svg width="12" height="14" viewBox="0 0 12 14"><path d="M6 0a5 5 0 0 1 5 5c0 4-5 9-5 9S1 9 1 5a5 5 0 0 1 5-5z" fill="#2b2b2b"/><circle cx="6" cy="5" r="1.8" fill="#fff"/></svg></span><span>2207 Maple Grove Lane<br>Fairview, CA 90210</span></div>
    <div class="item"><span class="dot"><svg width="12" height="12" viewBox="0 0 12 12"><path d="M2 1c.5-.5 1.1-.4 1.4.2l.8 1.4c.2.5.1.9-.2 1.2l-.5.5c.5 1.1 1.3 1.9 2.4 2.4l.5-.5c.3-.4.8-.4 1.2-.2l1.4.8c.6.3.7.9.2 1.4l-.7.7c-.6.6-1.6.7-2.4.2C3.9 8.1 2.3 6.6 1.2 4.4.7 3.6.8 2.6 1.4 2z" fill="#2b2b2b"/></svg></span><span>Call Us<br>555.014.2290</span></div>
    <div class="item"><span class="dot"><svg width="12" height="10" viewBox="0 0 12 10"><rect x="0" y="0" width="12" height="10" rx="1" fill="#2b2b2b"/><path d="M0.5 1l5.5 4 5.5-4" stroke="#fff" stroke-width="1.1" fill="none"/></svg></span><span>E mail Us<br>hello@lumakin.org</span></div>
  </div>
  <div class="foot-col abs" style="left:963px;top:48px">
    <h5>FOLLOW US</h5>
    <div class="item"><span class="dot"></span><span>Like us on<br>CIRCLEBOOK</span></div>
    <div class="item"><span class="dot"></span><span>Follow us on<br>CHIRPER</span></div>
    <div class="item"><span class="dot"></span><span>Follow us on<br>WORKLINK</span></div>
  </div>
  <div class="foot-line abs"></div>
  <div class="copy abs">Copyright © 2021 All Rights Reserved</div>
</footer>

</body>
</html>
```